Help design website for "Brightwater Civic Advisors" to advance the common good

Here is the Google doc link that lays out the design:

https://files.plumrivet.example/sheet/d/7QmTzR2wLx9KpVbN4hJcY8sEaUoFdG3iXkMnPq5rWt6/edit?usp=sharing

Here is the Google drive folder with the logos and photos: https://vault.plumrivet.example/open?id=4HkWp9LzQe2TxRvN8mBaYc3DsUoJfG6

The testimonials are being gathered and will be shared by Friday, 1/4.

The winner will also have to migrate the coding files to my hosting site.

Thank you for your help! Looking forward to seeing your designs.

Target Market(s)

Prospective clients

Industry/Entity Type

Non Profit

Coding

Coded - Design and coding required

Number of Pages Required

5+ page

Requirements
Must have
• Noted in the Google doc regarding layout.
Nice to have

```html
<!DOCTYPE html>
<html lang="en">
<head>
<meta charset="utf-8">
<title>About – Brightwater Civic Advisors</title>
<link rel="stylesheet" href="https://fonts.googleapis.com/css2?family=Poppins:wght@400;500;600;700&family=PT+Sans:wght@400;700&display=swap">
<style>
  :root {
    --blue: #3d87cb;
    --ink: #222222;
    --body: #2e2e2e;
    --white: #ffffff;
    --footer: #25252f;
    --pattern: #eeeef0;
    --rule: #4a4a56;
  }
  * { box-sizing: border-box; margin: 0; padding: 0; }
  html, body { width: 1200px; height: 2228px; overflow: hidden; background: var(--white); }
  body { position: relative; font-family: "PT Sans", Arial, sans-serif; color: var(--body); }

  .site-header { position: absolute; left: 0; top: 0; width: 1200px; height: 124px; background: var(--blue); }
  .brand { position: absolute; display: flex; align-items: center; gap: 12px; white-space: nowrap; }
  .brand-mark { flex: none; }
  .brand-name { font-family: "Poppins", Arial, sans-serif; font-weight: 600; }
  .site-header .brand { left: 145px; top: 44px; color: var(--white); }
  .site-header .brand-mark { width: 18px; height: 18px; background: var(--white); }
  .site-header .brand-name { font-size: 24px; line-height: 32px; }

  .cta { position: absolute; left: 736px; top: 21px; width: 319px; height: 42px; border: 2px solid var(--white); color: var(--white); font-family: "Poppins", Arial, sans-serif; font-weight: 600; font-size: 14px; display: flex; align-items: center; justify-content: center; text-decoration: none; }
  .main-nav { position: absolute; top: 86px; left: 562px; display: flex; gap: 27px; }
  .main-nav a { color: var(--white); font-family: "Poppins", Arial, sans-serif; font-weight: 600; font-size: 14px; text-decoration: none; padding-bottom: 4px; }
  .main-nav a.current { border-bottom: 2px solid var(--white); }
  .main-nav a.contact { margin-left: 10px; }

  .hero { position: absolute; left: 0; top: 124px; width: 1200px; height: 556px; }

  .portrait { position: absolute; left: 139px; top: 732px; width: 354px; height: 354px; border-radius: 50%; background: radial-gradient(circle at 50% 45%, #8a6f60 0%, #4a3a33 55%, #6f7a84 100%); box-shadow: 0 18px 40px rgba(0,0,0,0.25); }

  .about { position: absolute; left: 555px; top: 704px; width: 510px; }
  .about h1 { font-family: "Poppins", Arial, sans-serif; font-weight: 600; font-size: 26px; color: var(--ink); margin-bottom: 22px; }
  .about p { font-size: 16.5px; line-height: 20px; margin-bottom: 24px; }
  .about p.gap { margin-top: 14px; }
  .resume h2 { font-family: "Poppins", Arial, sans-serif; font-weight: 600; font-size: 25px; color: var(--ink); margin: 36px 0 12px; }
  .resume a { display: inline-flex; align-items: center; justify-content: center; width: 216px; height: 38px; background: var(--blue); color: var(--white); font-family: "Poppins", Arial, sans-serif; font-weight: 600; font-size: 15px; text-decoration: none; }

  .work { position: absolute; left: 0; top: 1420px; width: 1200px; height: 380px; }
  .work h2 { text-align: center; font-family: "Poppins", Arial, sans-serif; font-weight: 600; font-size: 26px; color: var(--ink); }
  .employer { position: absolute; display: flex; align-items: center; gap: 10px; font-family: "Poppins", Arial, sans-serif; font-weight: 600; font-size: 19px; line-height: 24px; transform: translateX(-50%); white-space: nowrap; }
  .employer .dot { width: 22px; height: 22px; flex: none; }
  .employer.maroon { color: #7a1f1f; } .employer.maroon .dot { background: #7a1f1f; }
  .employer.navy { color: #1c2a3a; } .employer.navy .dot { background: #2a8fd0; border-radius: 50%; }
  .employer.green { color: #5cb84a; }
  .employer.multi { color: #1f5f9e; } .employer.multi .dot { background: #e0a020; }
  .employer.blue { color: #3a55a8; } .employer.blue .dot { background: #3a55a8; }
  .badge { position: absolute; left: 538px; top: 245px; width: 124px; height: 124px; border-radius: 50%; background: #1a1a1a; border: 6px solid #dddddd; }

  .decor { position: absolute; left: 0; top: 0; }

  .site-footer .brand { left: 145px; top: 2094px; color: var(--white); }
  .site-footer .brand-mark { width: 22px; height: 22px; background: var(--blue); }
  .site-footer .brand-name { font-size: 27px; line-height: 36px; }
  .footer-divider { position: absolute; left: 612px; top: 2042px; width: 1px; height: 142px; background: var(--rule); }
  .footer-menu { position: absolute; left: 673px; top: 2058px; color: var(--white); }
  .footer-menu h3 { font-family: "Poppins", Arial, sans-serif; font-weight: 600; font-size: 12px; margin-bottom: 18px; }
  .footer-menu nav { font-family: "Poppins", Arial, sans-serif; font-size: 12px; }
  .footer-menu nav a { color: var(--white); text-decoration: none; }
  .footer-menu nav span { margin: 0 8px; }
  .copyright { font-family: "Poppins", Arial, sans-serif; font-size: 11px; margin-top: 44px; }
</style>
</head>
<body>

<svg class="decor" width="1200" height="2228" viewBox="0 0 1200 2228" aria-hidden="true">
  <rect x="0" y="1840" width="1200" height="180" fill="var(--pattern)"/>
  <polygon points="0,2020 600,1916 1200,2020 1200,2228 0,2228" fill="var(--footer)"/>
</svg>

<header class="site-header">
  <div class="brand">
    <span class="brand-mark"></span>
    <span class="brand-name">Brightwater Civic Advisors</span>
  </div>
  <a class="cta" href="#">BOOK A COMPLIMENTARY CONSULTATION</a>
  <nav class="main-nav">
    <a class="current" href="#">ABOUT</a>
    <a href="#">SERVICES &amp; TESTIMONIALS</a>
    <a href="#">MEDIA &amp; IMPACT</a>
    <a class="contact" href="#">CONTACT</a>
  </nav>
</header>

<svg class="hero" width="1200" height="556" viewBox="0 0 1200 556">
  <defs>
    <linearGradient id="heroTone" x1="0" y1="0" x2="1" y2="1">
      <stop offset="0" stop-color="#c9a04a"/>
      <stop offset="0.5" stop-color="#7a5a48"/>
      <stop offset="1" stop-color="#8a3a3a"/>
    </linearGradient>
  </defs>
  <rect role="img" aria-label="Photo of a group of people applauding at a civic engagement event podium" width="1200" height="556" fill="url(#heroTone)"/>
  <polygon points="0,542 600,440 1200,530 1200,556 0,556" fill="var(--blue)"/>
  <polygon points="0,556 600,452 1200,556" fill="var(--white)"/>
</svg>

<div class="portrait" role="img" aria-label="Portrait photo of founder Dana Reyes"></div>

<section class="about">
  <h1>About</h1>
  <p>Brightwater Civic Advisors supports nonprofit organizations and educational institutions to carry out their missions to benefit the wider community.</p>
  <p>Founder Dana Reyes is an educator with a 22-year record of demonstrated achievement and leadership roles in nonprofits and educational institutions. Most recently, she served as Associate Dean of Students in the University and Director of the Lakeshore Community Service Center at Lakeshore University. Dana has designed, implemented, and evaluated community-based learning and leadership training programs that have attained positive outcomes documented by survey results, recognition by outside agencies, and grants awarded for new initiatives and expansions. She has also significantly and consistently increased the number of program applicants, volunteers, and community partnerships through innovative programming, improved reputation, targeted recruitment, marketing and communications</p>
  <p class="gap">Dana is a native Chicagoan and has also lived in Tokyo, Boston, San Francisco, and Washington, DC. Dana received her bachelor of arts from Pinecrest College in Northfield, MN and her masters in education from Bayford University in Cambridge, MA</p>
  <div class="resume">
    <h2>Learn more about my experiences.</h2>
    <a href="#">DOWNLOAD MY RESUME</a>
  </div>
</section>

<section class="work">
  <h2>Work History</h2>
  <div class="employer maroon" style="left:246px; top:136px;"><span class="dot"></span>Lakeshore Community<br>Service Center</div>
  <div class="employer navy" style="left:587px; top:142px;"><span class="dot"></span>Meridian Fellows</div>
  <div class="employer green" style="left:909px; top:142px;">Harborline Public Schools</div>
  <div class="employer multi" style="left:262px; top:295px;"><span class="dot"></span>Civic Learners</div>
  <div class="badge" role="img" aria-label="Service program badge"></div>
  <div class="employer blue" style="left:920px; top:295px;"><span class="dot"></span>Pacific Exchange Teaching Program</div>
</section>

<footer class="site-footer">
  <div class="brand">
    <span class="brand-mark"></span>
    <span class="brand-name">Brightwater Civic Advisors</span>
  </div>
  <div class="footer-divider"></div>
  <div class="footer-menu">
    <h3>MENU</h3>
    <nav><a href="#">ABOUT</a><span>|</span><a href="#">SERVICES &amp; TESTIMONIALS</a><span>|</span><a href="#">MEDIA &amp; IMPACT</a><span>|</span><a href="#">CONTACT</a></nav>
    <p class="copyright">Copyrights @ 2019 All Rights Reserved</p>
  </div>
</footer>

</body>
</html>
```